Flyer for a Unique Type of Tax Services

Please refer to the attached sample design for reference. Feel free to change the wording as needed. Here is the project brief:

Objective:
Objective of this flyer is to introduce our services which we are launching soon, which is new of a kind, to our potential customers i.e. online tax return preparation. By looking at the flyer we want our target audience to get convinced of our services and visit our website and register with us. They don’t have to pay anything to register.

Our Competitors:
Currently there are three main options available to get tax returns prepared. First is to buy tax software and get tax return prepared at own, this is the cheapest option. There are studies that suggest that people who are not well aware of tax laws there are chances they miss certain tax refunds by filing returns at their own and potentially lose money. Second option is to go to the local offices of nation-wide tax service companies like P&L Fenwick and Morrow Quillan. They open offices only during tax season i.e. Jan through April but they are not available other part of the year and their association with the customers is temporary. Third option is to go to a CPA office which are the most expensive and very few people go for this option.

Weaknesses of the Current Options:
By self-preparing tax returns, there are chances that one can overlook certain tax laws that can provide additional tax credits and exemptions to people and overall they could have got a higher tax refund from the Govt. but they may miss it.
By going to other competitors during the peak time when tax returns are due, there are high chances that they don't have enough time to do research to ensure maximum refunds based on the exact circumstances of the individuals at the peak time as many people come to them during that time. Also they are not available after the tax season to provide them any answers to their questions or provide them tax planning tips to help them save tax in the next season.
By going to the CPA office, they charge a lot of fees and also for any tax advice later during the year, they will charge additional fees.

What we are offering:
We are offering a new option i.e. online tax return preparation through experts. We'll charge the fees competitive to what people are paying to local tax providers. But we will be different than our competitors as we'll be providing value added service if they got their returns prepared through us. Value added services we will be free of any additional cost for our customers who'll get tax return prepared through us.

Our Target Audience:
Our target audience is any person or couple who go to the tax service providers like P&L Fenwick or Morrow Quillan to get their tax returns prepared.

How We are Different:
Here is the summary of the unique aspects of our business as compared to the competitors:
- Customers just pay us the price for preparing the annual return and price is comparable and competitive to what they have been paying to other providers.
- Unlike our competitors, we do extensive research to review the circumstances of our customers and explore applicable tax laws to make sure all available tax credits, exemptions, and deductions are taken for our customers, whereas our customers don't usually do such kind of research as during the peak tax season when customers approach them they usually don’t have time to do that kind of research. We start our association with our customers much sooner than the actual due date and this provides us time to do extensive research and we try our best that our customers could get higher tax returns.
- By just getting tax returns prepared through us, we enter into a long-term association with our customers and provide them complimentary tax planning tips throughout the year to help them save tax in the following year
- We are available to our customers year-round to provide complementary answers to any tax related questions without any additional cost e.g. how to save tax when buying a car, whether to buy or lease the care to save tax, for the sole-proprietor business how to save tax by using portion of the home as home-office, how to save tax by using personal car for personal business.
- We also provide answers to other basic financial advise related matters e.g. which insurance product is better, whether full insurance or term-life insurance to chose, how to save for the retirement etc.

Other Details:
Our logo has already been designed and we want the same logo to be used in the flyer. Our website address is: www.LedgerPilotHub.com (it is still under construction but to get perspective of what we are trying to offer, visit this alternate website that it not final yet but will give an idea: http://www.ledgerpilothub.com/wordpress. Fyi, a video at this link is only a placeholder and not relevant to our services)

Requirements
Must have
• Please refer to the sample flyer attached. Feel free to change the design and language.
Should not have
• Please do not put any testimonial on the flyer as reflected in the under construction website.

```html
<!DOCTYPE html>
<html lang="en">
<head>
<meta charset="utf-8">
<title>LedgerPilot Hub – Tax Services Flyer</title>
<link href="https://fonts.googleapis.com/css2?family=Nunito:wght@700;800;900&family=Dancing+Script:wght@600&family=Open+Sans:wght@400;600&display=swap" rel="stylesheet">
<style>
  :root{
    --blue:#3a5bb5;
    --blue-dark:#2b4797;
    --red:#e0272b;
    --orange:#f26a21;
    --gray-text:#7d7d7d;
    --body-text:#555;
    --yellow:#ffe14a;
    --white:#fff;
  }
  *{margin:0;padding:0;box-sizing:border-box}
  html,body{width:848px;height:1200px;overflow:hidden;background:var(--white)}
  .flyer{position:relative;width:848px;height:1200px;overflow:hidden;background:var(--white);font-family:"Nunito",Arial,sans-serif}
  .backdrop{position:absolute;inset:0}
  .brand-box{position:absolute;left:38px;top:0;width:513px;height:167px;background:var(--white);display:flex;align-items:center;justify-content:center;gap:16px}
  .brand-mark{width:30px;height:30px;border-radius:50%;background:var(--orange)}
  .brand-name{font-weight:900;font-size:50px;color:var(--blue);letter-spacing:1px}
  .tag{position:absolute;left:-20px;height:52px;background:linear-gradient(90deg,var(--red),var(--orange));color:var(--white);font-weight:800;font-size:27px;display:flex;align-items:center;padding-left:64px;transform:rotate(-11deg);transform-origin:left center;box-shadow:0 2px 4px rgba(0,0,0,.25);white-space:nowrap}
  .tag-refund{top:385px;width:350px}
  .tag-tips{top:455px;width:420px}
  .tag-advice{top:572px;width:505px}
  .headline{position:absolute;left:0;top:664px;width:848px;text-align:center;color:var(--gray-text);font-weight:900;font-size:34.5px;line-height:35px;white-space:nowrap}
  .register{position:absolute;left:273px;top:846px;width:262px;text-align:center;color:var(--blue-dark);font-weight:900;font-size:26px;white-space:nowrap}
  .advisor-photo{position:absolute;left:36px;top:920px;width:240px;height:176px;background:linear-gradient(135deg,#c9b8a0,#8a7a68 60%,#d8d8d8)}
  .lead-script{position:absolute;left:184px;top:898px;font-family:"Dancing Script",cursive;font-weight:600;font-size:34px;color:var(--red);transform:rotate(-12deg);white-space:nowrap}
  .pitch{position:absolute;left:0;top:893px;width:640px;font-family:"Open Sans",Arial,sans-serif;font-size:18px;line-height:25px;color:var(--body-text)}
  .pitch span{display:block;text-align:justify;text-align-last:justify;white-space:nowrap}
  .l1,.l2{margin-left:406px}
  .l3{margin-left:378px}
  .l4{margin-left:311px}
  .l5,.l6,.l7,.l8{margin-left:292px}
  .badge{position:absolute;left:645px;top:885px;width:200px;height:200px}
  .badge-text{position:absolute;left:670px;top:912px;width:150px;text-align:center;color:var(--yellow);font-weight:900;line-height:1}
  .badge-text .b1{font-size:24px;display:block}
  .badge-text .b2{font-size:32px;display:block}
  .badge-text .b3{font-size:25px;display:block}
  .badge-text .b4{font-size:16px;color:var(--white);font-weight:800;display:block;line-height:18px;margin-top:2px}
  .footer{position:absolute;left:0;top:1111px;width:848px;height:89px;background:linear-gradient(90deg,var(--red),var(--orange));display:flex;align-items:center;padding-left:80px}
  .site{color:var(--white);font-family:"Open Sans",Arial,sans-serif;font-weight:600;font-size:42px}
</style>
</head>
<body>
<main class="flyer">
  <svg class="backdrop" width="848" height="1200" viewBox="0 0 848 1200">
    <defs>
      <radialGradient id="photoTone" cx="0.65" cy="0.4" r="0.7">
        <stop offset="0" stop-color="#8a8a8a"/>
        <stop offset="1" stop-color="#3a3a3a"/>
      </radialGradient>
      <linearGradient id="warm" x1="0" y1="0" x2="1" y2="0">
        <stop offset="0" stop-color="#e0272b"/>
        <stop offset="1" stop-color="#f26a21"/>
      </linearGradient>
    </defs>
    <path class="side-band" d="M0,0 H120 V600 Q40,560 0,520 Z" fill="#3a5bb5"/>
    <path class="right-band" d="M848,300 V1111 H790 Q840,900 800,640 Z" fill="#3a5bb5"/>
    <circle class="ring-blue" cx="440" cy="140" r="470" fill="#3a5bb5"/>
    <path class="ring-orange" d="M330,605 Q640,640 848,470 V520 Q640,690 330,620 Z" fill="url(#warm)"/>
    <circle class="hero-photo" cx="440" cy="140" r="450" fill="url(#photoTone)" role="img" aria-label="Photo: smiling woman in a white shirt and dark vest holding a blue umbrella against a grey wall covered with the word tax"/>
  </svg>

  <div class="brand-box">
    <span class="brand-mark"></span>
    <span class="brand-name">LedgerPilot Hub</span>
  </div>

  <div class="tag tag-refund">Maximum Refund?</div>
  <div class="tag tag-tips">Free Tax Planning Tips?</div>
  <div class="tag tag-advice">Complementary Tax Advice?</div>

  <h1 class="headline">Do you get these services free of cost<br>from your existing tax return<br>preparer and do they have time to<br>do extensive research to help you<br>get maximum refunds?</h1>
  <p class="register">Register Now Free</p>

  <div class="advisor-photo" role="img" aria-label="Photo: cheerful tax advisor at a desk with a calculator giving a thumbs up"></div>
  <span class="lead-script">And right away</span>
  <p class="pitch">
    <span class="l1">We'll start doing research</span>
    <span class="l2">for you to help you get</span>
    <span class="l3">maximum refund. And even after</span>
    <span class="l4">your return gets filed, we will be</span>
    <span class="l5">available year round, at no additional</span>
    <span class="l6">cost, to answer your tax related queries</span>
    <span class="l7">and provide you tax planning tips to</span>
    <span class="l8">help you save tax in the following year.</span>
  </p>

  <svg class="badge" viewBox="0 0 100 100">
    <polygon fill="url(#warm)" points="50,2 57,14 70,6 72,21 86,18 82,32 96,36 86,47 97,57 84,63 90,77 75,77 74,92 61,86 53,98 46,87 34,96 31,82 16,85 19,70 5,65 15,54 4,44 18,38 12,24 27,23 27,8 40,15"/>
  </svg>
  <div class="badge-text"><span class="b1">Free</span><span class="b2">Tax</span><span class="b3">Advice</span><span class="b4">round<br>the Year</span></div>

  <footer class="footer"><span class="site">www.LedgerPilotHub.com</span></footer>
</main>
</body>
</html>
```